SkyvornQ Business Cards and Stationary Design

Need a design for our business cards and stationary. I want to carry on the theme of the logo. I want the business cards to have a design on the back. I would like the business cards and the stationary to carry the same theme, design scheme, and branding

Target Market(s)

Airlines and Maintenance Facilities

Industry/Entity Type

Aviation

Contact Information for Business Card

Name
Position Title
Address: 4827 Trellis Hollow Road, Fort Pierce, Florida, 34951
Office Number
Mobile Number
Email
Website

Font styles to use
Serif
Sans Serif

Colors

Designer to choose colors to be used in the design.

```html
<!DOCTYPE html>
<html lang="en">
<head>
<meta charset="utf-8">
<title>SkyvornQ Business Cards</title>
<link href="https://fonts.googleapis.com/css2?family=Open+Sans:wght@300;400;700&display=swap" rel="stylesheet">
<style>
  :root {
    --navy: #14294d;
    --sky: #2a9fdc;
    --white: #ffffff;
    --backdrop-top: #ebeced;
    --backdrop-bottom: #d3d4d6;
    --edge: #222a33;
    --ink: #1d1f22;
  }
  * { margin: 0; padding: 0; box-sizing: border-box; }
  html, body { width: 1200px; height: 1096px; overflow: hidden; }
  body {
    position: relative;
    background: linear-gradient(160deg, var(--backdrop-top), var(--backdrop-bottom));
    font-family: "Open Sans", sans-serif;
    color: var(--ink);
  }
  .card {
    position: absolute;
    width: 815px;
    height: 466px;
    background: var(--white);
    border: 1px solid var(--edge);
    border-radius: 23px;
    overflow: hidden;
  }
  .card--front { left: 77px; top: 55px; }
  .card--back { left: 328px; top: 550px; }

  .brand-ring {
    position: absolute;
    border-radius: 50%;
    border-style: solid;
    border-color: var(--navy);
  }
  .card--front .brand-ring { left: 183px; top: 30px; width: 118px; height: 118px; border-width: 9px; }
  .wordmark {
    position: absolute;
    font-weight: 700;
    color: var(--navy);
    white-space: nowrap;
    line-height: 1;
  }
  .card--front .wordmark { left: 70px; top: 170px; font-size: 44px; letter-spacing: 7px; }

  .address {
    position: absolute;
    left: 70px; top: 244px;
    font-size: 17px;
    display: flex; align-items: center; gap: 7px;
  }
  .icon { width: 17px; height: 17px; flex: none; }

  .rule {
    position: absolute; left: 0; right: 0; top: 286px;
    height: 5px; background: var(--sky);
  }
  .band {
    position: absolute; left: 0; right: 0; top: 296px; bottom: 0;
    background: var(--navy);
    color: var(--white);
  }
  .notch {
    position: absolute; left: 112px; top: 289px;
    width: 36px; height: 20px;
  }
  .person { position: absolute; left: 65px; top: 48px; }
  .person__name { font-size: 27px; font-weight: 700; line-height: 1.2; }
  .person__title { font-size: 23px; font-weight: 300; line-height: 1.5; }
  .contacts {
    position: absolute; right: 38px; top: 31px;
    list-style: none; font-size: 18px; line-height: 29px;
  }
  .contacts li { display: flex; align-items: center; justify-content: flex-end; gap: 6px; }

  .card--back .brand-ring { left: 68px; top: 72px; width: 330px; height: 330px; border-width: 20px; }
  .card--back .wordmark { left: 438px; top: 176px; font-size: 40px; letter-spacing: 8px; }
  .web {
    position: absolute; left: 445px; top: 246px;
    font-size: 18px; letter-spacing: 4.3px; color: var(--ink);
  }
</style>
</head>
<body>
  <section class="card card--front" aria-label="Business card front">
    <div class="brand-ring" aria-hidden="true"></div>
    <div class="wordmark">SKYVORNQ</div>
    <p class="address">
      <svg class="icon" viewBox="0 0 20 20" aria-hidden="true"><circle cx="10" cy="10" r="8.5" fill="none" stroke="#2456a4" stroke-width="1.5"/><path d="M10 4.5a3.5 3.5 0 0 0-3.5 3.5c0 2.6 3.5 7 3.5 7s3.5-4.4 3.5-7A3.5 3.5 0 0 0 10 4.5z" fill="#2456a4"/><circle cx="10" cy="8" r="1.3" fill="#fff"/></svg>
      4827 Trellis Hollow Road, Fort Pierce, Florida, 34951
    </p>
    <div class="rule"></div>
    <div class="band">
      <div class="person">
        <p class="person__name">DORIAN HALVEK</p>
        <p class="person__title">PRESIDENT</p>
      </div>
      <ul class="contacts">
        <li><svg class="icon" viewBox="0 0 20 20" aria-hidden="true"><circle cx="10" cy="10" r="8.5" fill="none" stroke="#fff" stroke-width="1.5"/><path d="M7 5.5l1.6-.3 1 2.4-1 .9a6 6 0 0 0 2.9 2.9l.9-1 2.4 1-.3 1.6c-4 .6-8.1-3.5-7.5-7.5z" fill="#fff"/></svg>014-382-5907</li>
        <li><svg class="icon" viewBox="0 0 20 20" aria-hidden="true"><circle cx="10" cy="10" r="8.5" fill="none" stroke="#fff" stroke-width="1.5"/><rect x="7" y="5" width="6" height="10" rx="1" fill="none" stroke="#fff" stroke-width="1.4"/></svg>014-382-5907</li>
        <li><svg class="icon" viewBox="0 0 20 20" aria-hidden="true"><circle cx="10" cy="10" r="8.5" fill="none" stroke="#fff" stroke-width="1.5"/><rect x="5.5" y="7" width="9" height="6.5" fill="none" stroke="#fff" stroke-width="1.3"/><path d="M5.5 7l4.5 3.5L14.5 7" fill="none" stroke="#fff" stroke-width="1.3"/></svg>info@skyvornq.com</li>
        <li><svg class="icon" viewBox="0 0 20 20" aria-hidden="true"><g fill="none" stroke="#fff" stroke-width="1.4"><circle cx="10" cy="10" r="8.5"/><ellipse cx="10" cy="10" rx="3.8" ry="8.5"/><path d="M1.5 10h17M3 5.5h14M3 14.5h14"/></g></svg>www.skyvornq.com</li>
      </ul>
    </div>
    <svg class="notch" viewBox="0 0 36 20" aria-hidden="true"><path d="M0 0h36L18 17z" fill="#fff"/><path d="M0 0L18 17L36 0" fill="none" stroke="#2a9fdc" stroke-width="4"/></svg>
  </section>

  <section class="card card--back" aria-label="Business card back">
    <div class="brand-ring" aria-hidden="true"></div>
    <div class="wordmark">SKYVORNQ</div>
    <p class="web">www.skyvornq.com</p>
  </section>
</body>
</html>
```